Company Business Card (Company Promotions)

We want a Business Card that is both Elegant & High Class. We want the card stock thick and unique. We want it to build our Brand Name. We service Automobile dealerships & owners who drive luxury & exotic automobiles that cost an average of $75K. We provide towing services for Luxury & Exotic vehicles. Our colors are Black & Construction Yellow (Gold).
We are manufacture certified for Valdora Kent, RQT, PUKA, ELVO, Tavrine, HJ, Colvesi, Pendrel, Casteduvro, Ombra & Sorvanel. We have authorization to use their logo's.
Enclosed is our old business card. We only used the unusual & Unique brands on the cards but are open to the use of all of them. We also use the Federal Competence Badge that identifies our abilities.

Also enclosed is the name font that we use.

Target Market(s)

Business, Executive, Hi end people that drive finer luxury &/or exotic automobiles.

Industry/Entity Type

Business

Contact Information for Business Card

We market our name. Haul Crestmark. Business address is: 4812 Willowmere Lane, NE Ste: 210, Atlanta, GA 30399 Phone: 404-555-0148. Web address is crestmarkhaul-example.com
Manufacture Certified / Nationally Certified

Font styles to use
Other font styles liked:
• AR DESTINE (in Italic's)

Colors
ffc214

Requirements
Must have
• Must have the at least 5 of the manufacture logo's and the Guild Council Emblem (see on other business card)
Nice to have
• Place the manfacture logo's on the back.
Should not have
• No other colors than Black, Yellow & White

```html
<!DOCTYPE html>
<html lang="en">
<head>
<meta charset="utf-8">
<title>Haul Crestmark – Business Card</title>
<link rel="stylesheet" href="https://fonts.googleapis.com/css2?family=Audiowide&family=Open+Sans:wght@400;600&display=swap">
<style>
  :root {
    --black: #0b0b0b;
    --yellow: #ffc214;
    --white: #ffffff;
    --grey-text: #d8d8d8;
    --stage: #e8e5de;
  }
  * { box-sizing: border-box; margin: 0; padding: 0; }
  html, body { width: 1200px; height: 858px; overflow: hidden; }
  body {
    background: var(--stage);
    font-family: "Open Sans", sans-serif;
    position: relative;
  }
  .card {
    position: absolute;
    width: 560px;
    height: 320px;
    background: var(--black);
    overflow: hidden;
    box-shadow: 0 6px 18px rgba(0,0,0,.25);
  }
  .card--front { left: 40px; top: 269px; }
  .card--back  { left: 620px; top: 269px; }

  /* manufacturer strip */
  .brand-strip {
    position: absolute; left: 0; top: 0; bottom: 0; width: 92px;
    background: var(--yellow);
    display: flex; flex-direction: column; justify-content: space-around;
    align-items: center; padding: 10px 0;
    border-right: 4px solid var(--white);
  }
  .brand-strip__name {
    font-family: "Open Sans", sans-serif;
    font-weight: 600; font-size: 10px; color: var(--black);
    letter-spacing: .3px; white-space: nowrap;
  }

  .badge { position: absolute; }
  .card--front .badge { left: 118px; top: 28px; width: 92px; height: 104px; }
  .card--back .badge  { left: 34px; top: 26px; width: 86px; height: 96px; }

  .brand-name {
    font-family: "Audiowide", sans-serif;
    color: var(--yellow);
    white-space: nowrap;
    line-height: 1;
  }
  .card--front .brand-name {
    position: absolute; left: 228px; top: 48px; font-size: 34px;
  }
  .card--front .brand-rule {
    position: absolute; left: 228px; top: 96px; width: 300px; height: 3px;
    background: var(--yellow);
  }
  .tagline { color: var(--white); white-space: nowrap; }
  .card--front .tagline {
    position: absolute; left: 232px; top: 108px; font-size: 13px;
  }

  .contact {
    position: absolute; left: 232px; top: 176px;
    list-style: none; color: var(--grey-text); font-size: 14px; line-height: 1.55;
  }
  .contact__icons {
    position: absolute; left: 118px; top: 272px; display: flex; gap: 8px;
  }
  .contact__icons svg { width: 20px; height: 20px; }

  .card--back .brand-name {
    position: absolute; left: 0; right: 0; top: 138px; text-align: center; font-size: 52px;
  }
  .card--back .tagline {
    position: absolute; left: 0; right: 0; top: 214px; text-align: center; font-size: 16px;
  }
</style>
</head>
<body>

<section class="card card--front" aria-label="Card front">
  <div class="brand-strip">
    <span class="brand-strip__name">RQT</span>
    <span class="brand-strip__name">ELVO</span>
    <span class="brand-strip__name">Tavrine</span>
    <span class="brand-strip__name">Valdora Kent</span>
    <span class="brand-strip__name">Harrowmont</span>
    <span class="brand-strip__name">Pendrel</span>
    <span class="brand-strip__name">Fenwold</span>
    <span class="brand-strip__name">Lynxar</span>
    <span class="brand-strip__name">Trivena</span>
  </div>

  <svg class="badge" viewBox="0 0 92 104" role="img" aria-label="Federal Competence Badge">
    <path d="M6 10 Q46 -4 86 10 L86 52 Q80 86 46 102 Q12 86 6 52 Z" fill="#ffffff" stroke="#ffc214" stroke-width="3"/>
  </svg>

  <div class="brand-name">Haul Crestmark</div>
  <div class="brand-rule"></div>
  <div class="tagline">Manufacture Certified / Nationally Certified</div>

  <ul class="contact">
    <li>404-555-0148</li>
    <li>crestmarkhaul-example.com</li>
    <li>4812 Willowmere Lane, NE</li>
    <li>Ste: 210, Atlanta, GA 30399</li>
  </ul>

  <div class="contact__icons">
    <svg viewBox="0 0 20 20" aria-label="Phone">
      <rect width="20" height="20" rx="2" fill="#ffffff"/>
      <path d="M6 4 L8.5 4 L9.5 7 L8 8.2 Q9.5 11 11.8 12 L13 10.5 L16 11.5 L16 14 Q10 16 6 10 Q4.5 7 6 4 Z" fill="#0b0b0b"/>
    </svg>
    <svg viewBox="0 0 20 20" aria-label="Web">
      <rect width="20" height="20" rx="2" fill="#ffffff"/>
      <circle cx="10" cy="10" r="6" fill="none" stroke="#0b0b0b" stroke-width="1.4"/>
      <ellipse cx="10" cy="10" rx="2.6" ry="6" fill="none" stroke="#0b0b0b" stroke-width="1.2"/>
      <line x1="4" y1="10" x2="16" y2="10" stroke="#0b0b0b" stroke-width="1.2"/>
    </svg>
    <svg viewBox="0 0 20 20" aria-label="Address">
      <rect width="20" height="20" rx="2" fill="#ffffff"/>
      <path d="M10 4 L16 10 L14 10 L14 16 L6 16 L6 10 L4 10 Z" fill="#0b0b0b"/>
    </svg>
  </div>
</section>

<section class="card card--back" aria-label="Card back">
  <svg class="badge" viewBox="0 0 92 104" role="img" aria-label="Federal Competence Badge">
    <path d="M6 10 Q46 -4 86 10 L86 52 Q80 86 46 102 Q12 86 6 52 Z" fill="#ffffff" stroke="#ffc214" stroke-width="3"/>
  </svg>
  <div class="brand-name">Haul Crestmark</div>
  <div class="tagline">Manufacture Certified / Nationally Certified</div>
</section>

</body>
</html>
```